Business Card Design

We like to use greens as you will see in our logo (but not TOO much green). We are a Dental Clinic in a somewhat eccentric community. We do not like the dated sharp designs which we see many dentists use. We're looking for something bright and fresh while still maintaining the integrity of the profession. Elegance is not necessarily what we are going for... we need for the design to be "mature" but also up-lifting.

See our logo.
Updates

Project Deadline Extended
Reason: We have 5 designs which we like. But we'd like to see a few more before committing to a design.

Project Deadline Extended
Reason: We are awaiting revisions to this project. We are still welcoming designs while we wait to see if designers are able to provide to us the revisions we require in order to proceed with a selection.

Target Market(s)

Younger families - ages late 20's to early 40's

Industry/Entity Type

Business

Contact Information for Business Card

Corwel T. Banfry DDS 2730 W. Halvert Rd. Ste. 7 Royal Oak, MI 48391 (248)555-0174 FX (248)555-0189 info@BrightwellDentalCareMi.com BrigthwellDentalCareMi.com on the back of the card we need an appointment reminder (For____ Date___ Time____) with "If you are unable to keep your appointment, kindly give 48 hours notice" at the bottom. No use of teeth in the design. DOUBLE SIDED DESIGN

Requirements
Should not have
• The use of pictures of teeth

```html
<!DOCTYPE html>
<html lang="en">
<head>
<meta charset="utf-8">
<title>Brightwell Dental Care – Business Card</title>
<link rel="stylesheet" href="https://fonts.googleapis.com/css2?family=Open+Sans:ital,wght@0,400;0,600;0,700;1,600&family=Cinzel:wght@500&display=swap">
<style>
  :root {
    --green-dark: #1e6b35;
    --green-mid: #2e8a3e;
    --green-light: #8cc63f;
    --ink: #222222;
    --card: #ffffff;
    --backdrop: #e9ebe8;
    --line: #9a9a9a;
  }
  * { box-sizing: border-box; margin: 0; padding: 0; }
  html, body { width: 1200px; height: 1178px; overflow: hidden; }
  body {
    background: var(--backdrop);
    font-family: "Open Sans", Arial, sans-serif;
    color: var(--ink);
    position: relative;
  }
  .card {
    position: absolute;
    background: var(--card);
    box-shadow: 0 3px 10px rgba(0,0,0,0.25);
    overflow: hidden;
  }
  .card--front { left: 36px; top: 49px; width: 916px; height: 518px; }
  .card--back  { left: 241px; top: 615px; width: 916px; height: 522px; }

  /* Front */
  .brand {
    position: absolute; left: 40px; top: 200px;
    color: var(--green-dark); font-weight: 600; line-height: 1;
  }
  .brand__name { font-size: 80px; letter-spacing: -1px; display: block; }
  .brand__sub { font-size: 40px; display: block; margin-top: 12px; letter-spacing: 1px; }
  .brand__dot {
    position: absolute; left: 175px; top: -95px;
    width: 76px; height: 76px; border-radius: 50%;
    background: var(--green-light);
  }
  .divider {
    position: absolute; left: 500px; top: 104px; width: 2px; height: 235px;
    background: var(--line);
  }
  .contact { position: absolute; left: 520px; top: 98px; width: 376px; }
  .contact__name { color: var(--green-dark); font-size: 32px; font-weight: 700; line-height: 1.2; }
  .contact__title { font-size: 23px; margin-top: 2px; }
  .contact__list { list-style: none; margin-top: 24px; }
  .contact__list li {
    font-size: 19px; line-height: 1; margin-bottom: 22px; white-space: nowrap;
    display: flex; align-items: center; gap: 6px;
  }
  .contact__list svg { width: 17px; height: 17px; fill: var(--green-dark); flex: none; }
  .address { position: absolute; left: 22px; top: 440px; font-size: 18px; }
  .footer-band { position: absolute; left: 0; bottom: 0; width: 916px; height: 70px; }
  .website {
    position: absolute; right: 16px; bottom: 10px;
    color: #ffffff; font-size: 22px; letter-spacing: 1.5px;
  }

  /* Back */
  .appt__title {
    position: absolute; left: 0; right: 0; top: 85px; text-align: center;
    font-family: "Cinzel", Georgia, serif; font-size: 36px; color: var(--green-dark);
  }
  .field { position: absolute; font-size: 24px; display: flex; align-items: baseline; }
  .field__dots { display: inline-block; border-bottom: 3px dotted #555; height: 1px; margin: 0 10px; }
  .field--name { left: 72px; top: 150px; }
  .field--date { left: 72px; top: 216px; }
  .next { position: absolute; left: 72px; top: 282px; display: flex; align-items: center; }
  .next__label { font-size: 24px; width: 252px; }
  .next__box {
    width: 165px; height: 36px; border: 2px solid #555; border-radius: 5px; margin-right: 12px;
  }
  .days { position: absolute; left: 68px; top: 370px; display: flex; align-items: center; }
  .day { display: flex; align-items: center; font-weight: 700; font-size: 24px; margin-right: 14px; }
  .day__box {
    width: 55px; height: 35px; border: 2px solid #555; border-radius: 4px; margin-left: 8px;
  }
  .appt__notice {
    position: absolute; left: 0; right: 0; top: 448px; text-align: center;
    font-style: italic; font-weight: 600; font-size: 23px;
  }
</style>
</head>
<body>
  <article class="card card--front">
    <div class="brand">
      <span class="brand__dot"></span>
      <span class="brand__name">Brightwell</span>
      <span class="brand__sub">DENTAL CARE</span>
    </div>
    <div class="divider"></div>
    <div class="contact">
      <p class="contact__name">Corwel T. Banfry</p>
      <p class="contact__title">DDS</p>
      <ul class="contact__list">
        <li>
          <svg viewBox="0 0 20 20" aria-label="Phone"><path d="M5 2l3 4-2 2c1 2 3 4 5 5l2-2 4 3-2 3C9 17 3 11 2 5z"/></svg>
          (248)555-0174
        </li>
        <li>
          <svg viewBox="0 0 20 20" aria-label="Fax"><path d="M5 3h8v4H5zM2 8h16v8h-3v-3H5v3H2zM6 14h8v4H6z"/></svg>
          (248)555-0189
        </li>
        <li>
          <svg viewBox="0 0 20 20" aria-label="Email"><path d="M2 5h16v11H2zM3 6l7 5 7-5"/></svg>
          info@BrightwellDentalCareMi.com
        </li>
      </ul>
    </div>
    <p class="address">2730 W. Halvert Rd. Ste. 7 Royal Oak, MI 48391</p>
    <svg class="footer-band" viewBox="0 0 916 70" preserveAspectRatio="none" aria-hidden="true">
      <path d="M0 20 H500 C540 20 560 0 620 0 H916 V70 H0 Z" fill="var(--green-dark)"/>
      <path d="M0 26 H505 C545 26 565 8 625 8 H916" stroke="var(--green-light)" stroke-width="5" fill="none"/>
      <path d="M0 34 H510 C550 34 570 16 630 16 H916" stroke="#ffffff" stroke-width="4" fill="none"/>
    </svg>
    <p class="website">www.brigthwelldentalcaremi.com</p>
  </article>

  <article class="card card--back">
    <h2 class="appt__title">YOUR APPOINTMENT</h2>
    <div class="field field--name">Name :<span class="field__dots" style="width:670px"></span></div>
    <div class="field field--date">Date :<span class="field__dots" style="width:230px"></span>Time :<span class="field__dots" style="width:250px"></span>am / pm</div>
    <div class="next">
      <span class="next__label">Next Appointment</span>
      <span class="next__box"></span><span class="next__box"></span><span class="next__box"></span>
    </div>
    <div class="days">
      <span class="day">MON<span class="day__box"></span></span>
      <span class="day">TUE<span class="day__box"></span></span>
      <span class="day">WED<span class="day__box"></span></span>
      <span class="day">THU<span class="day__box"></span></span>
      <span class="day">FRI<span class="day__box"></span></span>
      <span class="day">SAT<span class="day__box"></span></span>
    </div>
    <p class="appt__notice">If you are unable to keep your appointment, kindly give 48 hours notice</p>
  </article>
</body>
</html>
```